New hardcover book cover

I want a striking, eye-catching cover with title, subtitle and a picture.See for previous book covers: www.brightquillpress.com

Target Market(s)

young, successful entrepreneurs that have built a business in a niche market that they discovered.

Font styles to use
Serif

Colors

Designer to choose colors to be used in the design.

Requirements
Must have
• A book cover that impresses and captures the imagination of those who look at it.
• MY MISTAKE, SORRY.
• Title: Founders Behind the Quiet Trade Boom
• Subtitle: 25 stories of success from
• discovering hidden opportunities
• Author: Dennis Harlow
• Please use the photo attached, thanks.

```html
<!DOCTYPE html>
<html lang="en">
<head>
<meta charset="utf-8">
<title>Founders Behind the Quiet Trade Boom — Book Cover</title>
<link rel="stylesheet" href="https://fonts.googleapis.com/css2?family=Anton&family=Josefin+Sans:wght@300;400&display=swap">
<style>
  :root {
    --page-bg: #262626;
    --cover-dark: #17121a;
    --cover-pink: #d8265f;
    --cover-rose: #c42a5c;
    --cover-steel: #6f7480;
    --flame-orange: #f39a3c;
    --flame-gold: #ffc766;
    --title-white: #f2f0ef;
    --accent-pink: #e0245e;
  }
  * { margin: 0; padding: 0; box-sizing: border-box; }
  html, body {
    width: 1200px;
    height: 905px;
    overflow: hidden;
    background: var(--page-bg);
  }
  .canvas {
    position: relative;
    width: 1200px;
    height: 905px;
  }
  .book-cover {
    position: absolute;
    left: 335px;
    top: 22px;
    width: 530px;
    height: 860px;
    overflow: hidden;
    background: var(--cover-dark);
  }
  .cover-photo {
    position: absolute;
    inset: 0;
    background:
      radial-gradient(ellipse 55% 30% at 55% 18%, rgba(255, 199, 102, 0.85), rgba(243, 154, 60, 0.55) 45%, rgba(243, 154, 60, 0) 75%),
      radial-gradient(ellipse 60% 35% at 10% 48%, rgba(216, 38, 95, 0.95), rgba(196, 42, 92, 0.6) 55%, rgba(196, 42, 92, 0) 85%),
      radial-gradient(ellipse 45% 55% at 88% 50%, rgba(111, 116, 128, 0.85), rgba(111, 116, 128, 0) 80%),
      linear-gradient(180deg, #2a1d24 0%, #5a2a3c 30%, #8a2c52 50%, #3b2633 68%, var(--cover-dark) 82%);
  }
  .author-name {
    position: absolute;
    top: 62px;
    left: 0;
    right: 0;
    text-align: center;
    font-family: "Josefin Sans", sans-serif;
    font-weight: 300;
    font-size: 34px;
    letter-spacing: 0.16em;
    color: var(--title-white);
    text-transform: uppercase;
  }
  .title-block {
    position: absolute;
    top: 500px;
    left: 0;
    right: 0;
    display: flex;
    flex-direction: column;
    align-items: center;
    font-family: "Anton", sans-serif;
    color: var(--title-white);
    text-transform: uppercase;
    line-height: 0.95;
  }
  .title-top { font-size: 46px; letter-spacing: 0.01em; }
  .title-row {
    display: flex;
    align-items: center;
    gap: 10px;
  }
  .title-small {
    display: flex;
    flex-direction: column;
    font-size: 22px;
    line-height: 0.9;
    text-align: right;
  }
  .title-mid { font-size: 64px; }
  .title-dash {
    width: 48px;
    height: 7px;
    background: var(--title-white);
    margin: 0 22px;
  }
  .title-accent {
    font-size: 100px;
    color: var(--accent-pink);
    line-height: 1;
  }
  .subtitle {
    position: absolute;
    top: 782px;
    left: 0;
    right: 0;
    text-align: center;
    font-family: "Josefin Sans", sans-serif;
    font-weight: 400;
    font-size: 18px;
    letter-spacing: 0.02em;
    line-height: 1.4;
    color: var(--title-white);
    text-transform: uppercase;
  }
</style>
</head>
<body>
  <div class="canvas">
    <div class="book-cover">
      <div class="cover-photo" role="img" aria-label="Photo of a flaming dart striking the centre of a pink and grey dartboard target"></div>
      <div class="author-name">Dennis Harlow</div>
      <div class="title-block">
        <div class="title-top">Founders</div>
        <div class="title-row">
          <div class="title-small"><span>Behind</span><span>the</span></div>
          <div class="title-mid">Quiet</div>
        </div>
        <div class="title-row">
          <span class="title-dash"></span>
          <div class="title-mid">Trade</div>
          <span class="title-dash"></span>
        </div>
        <div class="title-accent">Boom</div>
      </div>
      <p class="subtitle">25 captivating stories of success<br>from discovering hidden opportunities</p>
    </div>
  </div>
</body>
</html>
```